Larkspur Cosmetics Website needs a professional upgrade

I need a new design for an online cosmetics store that looks professional and clean but also has a natural look and feel to it.

The women in the top bar (Image attached) needs to be included and she is on all of our advertising banners/ stands though I would like to come away from the black.

Design Needs:
- 1 x Home Page
- 1 x Products Page

I have plenty more website coming along so hopefully can find someone who I can rely on for a quick turnover :)

Happy designing !

Industry/Entity Type

Store

Number of Pages Required

2 page

Font styles to use
Sans Serif

Requirements
Must have
• - Natural Clean look
Should not have
• - The current black and green colours

```html
<!DOCTYPE html>
<html lang="en">
<head>
<meta charset="utf-8">
<title>Larkspur Cosmetics — Make-Up</title>
<link rel="stylesheet" href="https://fonts.googleapis.com/css2?family=Roboto:wght@400;500;700&family=Roboto+Condensed:wght@400;700&display=swap">
<style>
:root{
  --bg:#5b5b5b; --dark:#333333; --white:#ffffff; --rule:#e6e6e6; --soft:#f5f5f5;
  --accent:#f15b67; --price:#e5192e; --text:#333333; --muted:#666666; --star:#f5a623; --star-off:#d0d0d0;
}
*{box-sizing:border-box;margin:0;padding:0}
html,body{width:1200px;height:1200px;overflow:hidden;background:var(--bg)}
body{font-family:"Roboto",Arial,sans-serif;color:var(--text)}
.stage{position:relative;width:1500px;height:1500px;transform:scale(.8);transform-origin:0 0}
.abs{position:absolute}
.page{position:absolute;left:286px;top:0;width:929px;height:1500px;background:var(--white)}
.topbar{position:absolute;left:286px;top:0;width:929px;height:25px;background:var(--dark);color:#fff;font-size:11px}
.topbar span{position:absolute;top:7px}
.brand{position:absolute;left:348px;top:40px;font-size:17px;font-weight:500;color:var(--text);display:flex;align-items:center;gap:8px}
.brand i{width:18px;height:18px;background:var(--accent);display:block}
.cart{left:922px;top:50px;font-size:13px;color:var(--muted)}
.hotline{left:1015px;top:59px;font-size:13px;color:var(--muted)}
.hotline b{color:var(--text);font-weight:500;margin-left:6px}
.box{position:absolute;border:1px solid var(--rule);background:#fff}
.cats{left:348px;top:104px;width:191px;height:35px;font-size:14px;display:flex;align-items:center;padding-left:14px;gap:14px}
.search{left:560px;top:104px;width:434px;height:28px;font-size:10px;color:var(--muted);padding:8px 16px}
.search .go{position:absolute;right:-1px;top:-1px;width:31px;height:28px;background:var(--accent)}
.btn{position:absolute;top:104px;height:28px;border:1px solid var(--rule);font-size:10px;color:var(--muted);display:flex;align-items:center;justify-content:center;gap:5px}
.hrule{position:absolute;left:286px;top:140px;width:929px;height:2px;background:var(--soft)}
.crumb{left:349px;top:152px;font-size:9px}
.crumb em{font-style:normal;color:var(--accent)}
.side h3,.heading{font-size:13px;font-weight:400;text-transform:uppercase}
.filter{font-size:10px;color:var(--muted);line-height:17.2px}
.filter div{display:flex;align-items:center;gap:7px}
.filter div::before{content:"";width:9px;height:9px;border:1px solid #ccc;display:block}
.label{font-size:10px;text-transform:uppercase}
.toolbar{position:absolute;left:560px;width:594px;height:35px;border:1px solid var(--rule);font-size:9px;color:var(--text)}
.toolbar .sel{position:absolute;top:8px;border:1px solid var(--rule);height:19px;padding:4px 6px}
.pg{position:absolute;top:8px;width:19px;height:19px;border:1px solid var(--rule);text-align:center;line-height:17px;font-size:8px}
.pg.on{background:var(--accent);color:#fff;border-color:var(--accent)}
.grid-ic{position:absolute;left:7px;top:11px;width:12px;height:12px;background:var(--accent)}
.list-ic{position:absolute;left:28px;top:11px;width:13px;height:12px;background:repeating-linear-gradient(#666 0 3px,#fff 3px 4.5px)}
.card{position:absolute;width:185px;border:1px solid var(--rule);background:#fff}
.card .pic{position:absolute;left:20px;top:8px;width:145px;height:130px;border-radius:6px}
.card .name{position:absolute;left:7px;top:150px;width:110px;font-family:"Roboto Condensed",Arial,sans-serif;font-size:11px;line-height:11.5px}
.card .price{position:absolute;right:7px;top:147px;font-family:"Roboto Condensed",Arial,sans-serif;font-size:14px;font-weight:700;color:var(--price)}
.old{position:absolute;right:7px;top:166px;font-size:10px;color:#999;text-decoration:line-through}
.stars{font-size:12px;letter-spacing:1.5px;color:var(--star-off)}
.stars b{color:var(--star);font-weight:400}
.card .stars{position:absolute;left:6px}
.sale{position:absolute;right:7px;top:7px;width:37px;height:37px;border-radius:50%;background:#4dc3c6;color:#fff;font-size:10px;text-align:center;line-height:37px}
.ship{left:348px;top:877px;width:191px;height:61px;background:var(--accent);color:#fff;font-family:"Roboto Condensed",Arial,sans-serif;font-size:10px;line-height:16px;padding:16px 0 0 77px}
.tab{position:absolute;top:961px;width:33px;height:27px;background:var(--accent)}
.mini .pic{position:absolute;width:50px;height:55px;border-radius:4px}
.mini .t{position:absolute;font-family:"Roboto Condensed",Arial,sans-serif;font-size:11px}
.mini .p{position:absolute;font-family:"Roboto Condensed",Arial,sans-serif;font-size:14px;font-weight:700;color:var(--price)}
.footer{position:absolute;left:286px;top:1215px;width:929px;height:257px;background:var(--soft)}
.news{position:absolute;left:560px;top:1215px;width:655px;height:68px;background:#f0f0f0}
.fcol h4{font-size:11px;font-weight:500;text-transform:uppercase;color:var(--text)}
.fcol h4::after{content:"";display:block;width:20px;height:2px;background:var(--accent);margin-top:7px}
.fcol ul{list-style:none;font-size:8.5px;color:var(--muted);line-height:17.2px;margin-top:10px}
.ftext{font-size:8.5px;color:var(--muted);line-height:13.5px}
.soc{position:absolute;top:1438px;width:20px;height:20px;border-radius:50%}
.copy{position:absolute;left:286px;top:1472px;width:929px;height:28px;background:var(--dark);color:#fff;font-size:9px;padding:9px 62px}
.pay{position:absolute;top:1479px;width:24px;height:15px;border-radius:2px;background:#8a8a8a}
</style>
</head>
<body>
<div class="stage">
  <div class="page"></div>
  <div class="topbar"><span style="left:733px">My Account</span><span style="left:815px">My Wishlist</span></div>

  <div class="brand"><i></i>Larkspur Cosmetics</div>

  <div class="abs cart">
    <svg width="22" height="20" viewBox="0 0 22 20" style="vertical-align:middle"><path d="M1 3h4l3 10h10l2-7H6" fill="none" stroke="#f15b67" stroke-width="1.6"/><circle cx="9" cy="17" r="1.6" fill="#f15b67"/><circle cx="17" cy="17" r="1.6" fill="#f15b67"/></svg>
    <span style="position:absolute;left:18px;top:-4px;width:10px;height:10px;background:#f5a623;border-radius:2px;color:#fff;font-size:7px;text-align:center;line-height:10px">0</span>
    <span style="margin-left:4px">My Cart</span>
  </div>
  <div class="abs" style="left:1004px;top:56px;width:1px;height:22px;background:var(--rule)"></div>
  <div class="abs hotline">
    <svg width="14" height="14" viewBox="0 0 14 14" style="vertical-align:-2px;margin-right:9px"><path d="M3 1l2 3-1.5 1.5a8 8 0 0 0 5 5L10 9l3 2-1.5 2.5C6 13 1 8 .5 2.5z" fill="#f15b67"/></svg>Hotline:<b>1900 5521</b>
  </div>

  <div class="box cats">
    <svg width="12" height="10"><rect width="12" height="2" fill="#333"/><rect y="4" width="12" height="2" fill="#333"/><rect y="8" width="12" height="2" fill="#333"/></svg>CATEGORIES
  </div>
  <div class="box search">All Categories
    <div class="go"><svg width="31" height="28"><circle cx="14" cy="12" r="6" fill="none" stroke="#fff" stroke-width="2"/><path d="M18 16l5 5" stroke="#fff" stroke-width="2"/></svg></div>
  </div>
  <div class="btn" style="left:1002px;width:73px"><svg width="14" height="12"><circle cx="5" cy="4" r="3" fill="#555"/><path d="M0 12a5 5 0 0 1 10 0z" fill="#555"/></svg>Register</div>
  <div class="btn" style="left:1082px;width:72px"><svg width="11" height="11"><circle cx="5.5" cy="5.5" r="5" fill="#555"/></svg>Login</div>
  <div class="hrule"></div>

  <div class="abs crumb">Home <em>&nbsp;»&nbsp; Make-Up</em></div>

  <!-- Sidebar filters -->
  <div class="box side" style="left:348px;top:178px;width:191px;height:431px">
    <h3 class="abs" style="left:13px;top:10px">Shop By</h3>
    <div class="abs" style="left:13px;top:35px;width:163px;height:1px;background:var(--rule)"></div>
    <div class="abs label" style="left:13px;top:48px">Category</div>
    <div class="abs filter" style="left:13px;top:63px">
      <div>Hair (11)</div><div>Eyes (11)</div><div>Face (19)</div><div>Simple (14)</div><div>Cosmetics (15)</div><div>Mascara (12)</div><div>Tools (15)</div><div>Trends (12)</div><div>Nail (12)</div>
    </div>
    <div class="abs" style="left:13px;top:226px;width:163px;height:1px;background:var(--accent);opacity:.5"></div>
    <div class="abs label" style="left:13px;top:239px">Price</div>
    <div class="abs" style="left:17px;top:264px;width:155px;height:2px;background:#ccc"></div>
    <div class="abs" style="left:13px;top:261px;width:8px;height:8px;background:#888"></div>
    <div class="abs" style="left:167px;top:261px;width:8px;height:8px;background:#888"></div>
    <div class="abs" style="left:13px;top:278px;font-size:10px;color:var(--muted)">$10</div>
    <div class="abs" style="left:153px;top:278px;font-size:10px;color:var(--muted)">$178</div>
    <div class="abs" style="left:13px;top:296px;width:163px;height:1px;background:var(--rule)"></div>
    <div class="abs label" style="left:13px;top:310px">Manufacturer</div>
    <div class="abs filter" style="left:13px;top:324px">
      <div>Alderwood</div><div>Birch Lane</div><div>Corvin Hale</div><div>Delmare</div><div>Estova</div>
    </div>
  </div>

  <!-- Best seller -->
  <div class="box" style="left:348px;top:630px;width:191px;height:226px">
    <h3 class="abs heading" style="left:13px;top:16px">Best Seller</h3>
    <svg class="abs" style="left:14px;top:90px" width="12" height="22"><path d="M11 1L2 11l9 10" fill="none" stroke="#666" stroke-width="2"/></svg>
    <svg class="abs" style="left:162px;top:90px" width="12" height="22"><path d="M1 1l9 10-9 10" fill="none" stroke="#666" stroke-width="2"/></svg>
    <div class="abs" role="img" aria-label="Pink perfume bottle beside its box" style="left:42px;top:50px;width:96px;height:108px;border-radius:8px;background:linear-gradient(135deg,#f7e1e8,#eaa9c0)"></div>
    <div class="abs" style="left:13px;top:175px;font-family:'Roboto Condensed',sans-serif;font-size:11px">Simple product</div>
    <div class="abs" style="left:136px;top:172px;font-family:'Roboto Condensed',sans-serif;font-size:14px;font-weight:700;color:var(--price)">$87.00</div>
    <div class="abs stars" style="left:13px;top:190px"><b>★★</b>★★★</div>
  </div>

  <div class="abs ship">
    <svg class="abs" style="left:12px;top:12px" width="58" height="36"><rect x="1" y="4" width="34" height="22" rx="2" fill="#fff"/><path d="M36 11h10l8 9v6H36z" fill="#fff"/><circle cx="12" cy="29" r="5" fill="#fff" stroke="#f15b67" stroke-width="2"/><circle cx="45" cy="29" r="5" fill="#fff" stroke="#f15b67" stroke-width="2"/></svg>
    <b style="color:#ffe3a0">FREE</b> <b>SHIPPING</b><br>ON ALL ORDERS OVER $50
  </div>

  <div class="tab" style="left:348px;width:34px;background:#fff;border-top:2px solid var(--accent)"></div>
  <div class="tab" style="left:383px"></div>
  <div class="tab" style="left:416px"></div>
  <div class="tab" style="left:450px"></div>
  <div class="box mini" style="left:348px;top:988px;width:191px;height:220px">
    <div class="pic" role="img" aria-label="Pink perfume bottle" style="left:16px;top:10px;background:linear-gradient(135deg,#f7e3ea,#e9b2c6)"></div>
    <div class="t" style="left:82px;top:20px">Simple product</div><div class="p" style="left:82px;top:33px">$87.00</div>
    <div class="abs" style="left:14px;top:72px;width:162px;height:1px;background:var(--rule)"></div>
    <div class="pic" role="img" aria-label="Gold-capped perfume bottle" style="left:16px;top:82px;background:linear-gradient(135deg,#fbefe2,#e8c79a)"></div>
    <div class="t" style="left:82px;top:92px">Vopi jare mase lamas</div><div class="p" style="left:82px;top:106px">$99.00</div>
    <div class="abs" style="left:14px;top:145px;width:162px;height:1px;background:var(--rule)"></div>
    <div class="pic" role="img" aria-label="Violet perfume bottle" style="left:16px;top:155px;background:linear-gradient(135deg,#e6e3f3,#8e86c8)"></div>
    <div class="t" style="left:82px;top:165px">Vurem moren tikas</div><div class="p" style="left:82px;top:179px">$77.00</div>
  </div>

  <!-- Product list -->
  <h1 class="abs heading" style="left:557px;top:173px;font-size:14px">Make-Up</h1>

  <div class="toolbar" style="top:203px;border-top:2px solid var(--accent)">
    <div class="grid-ic"></div><div class="list-ic"></div>
    <span class="abs" style="left:58px;top:12px">Sort by</span>
    <div class="sel" style="left:89px;width:65px">Position ▾</div>
    <span class="abs" style="left:157px;top:8px;font-size:11px">↓</span>
    <span class="abs" style="left:396px;top:12px">Show</span>
    <div class="sel" style="left:425px;width:30px">12 ▾</div>
    <span class="abs" style="left:461px;top:12px">per page</span>
    <div class="pg on" style="left:503px">1</div><div class="pg" style="left:525px">2</div><div class="pg" style="left:546px">3</div><div class="pg" style="left:567px">›</div>
  </div>

  <div class="card" style="left:560px;top:259px;height:198px">
    <div class="pic" role="img" aria-label="Pink boxed serum with white bottle" style="background:linear-gradient(135deg,#f6dbe6,#ebe6ea)"></div>
    <div class="name">Cilas kiren maren</div><div class="price">$76.00</div>
    <div class="stars" style="top:168px"><b>★★★★</b>★</div>
  </div>
  <div class="card" style="left:765px;top:259px;height:198px">
    <div class="pic" role="img" aria-label="Amber perfume bottle beside a cream box" style="background:linear-gradient(135deg,#f1ece2,#f3c646)"></div>
    <div class="name">Mase pola taki</div><div class="price">$32.00</div>
    <div class="stars" style="top:168px"><b>★★★</b>★★</div>
  </div>
  <div class="card" style="left:970px;top:259px;height:198px">
    <div class="pic" role="img" aria-label="Blue body lotion bottle" style="left:60px;width:65px;background:linear-gradient(#2f4ea8,#5d7ed0)"></div>
    <div class="name">Simas kiten rugas</div><div class="price">$78.00</div>
    <div class="stars" style="top:168px"><b>★★★★</b>★</div>
  </div>

  <div class="card" style="left:560px;top:481px;height:198px">
    <div class="pic" role="img" aria-label="Row of lipsticks in pink and red" style="background:linear-gradient(#e84f66,#d57a8a 45%,#222 46%,#3a3a3a)"></div>
    <div class="name">Seca enmas tiren</div><div class="price">$88.00</div>
    <div class="stars" style="top:168px"><b>★★★</b>★★</div>
  </div>
  <div class="card" style="left:765px;top:481px;height:198px">
    <div class="pic" role="img" aria-label="Three round blush compacts" style="background:radial-gradient(circle at 40% 35%,#f06a6a,#f5a36b 50%,#e8e46a 80%,#fff)"></div>
    <div class="name">Umas tilan pokan</div><div class="price">$76.00</div>
    <div class="stars" style="top:168px"><b>★★</b>★★★</div>
  </div>
  <div class="card" style="left:970px;top:481px;height:209px">
    <div class="pic" role="img" aria-label="Pink cream tube with gold cap" style="left:60px;width:65px;background:linear-gradient(#f8c9c4,#f3a8a8 85%,#b98a3a)"></div>
    <div class="name">Goten maze simas laten</div><div class="price">$76.00</div>
    <div class="stars" style="top:180px"><b>★★★</b>★★</div>
  </div>

  <div class="card" style="left:560px;top:703px;height:198px">
    <div class="pic" role="img" aria-label="Clear turquoise toner bottle" style="left:60px;width:65px;background:linear-gradient(#8fd6e0,#4cb9cf)"></div>
    <div class="sale">Sale</div>
    <div class="name">Jiten milas polan mase</div><div class="price">$55.00</div><div class="old">$65.00</div>
    <div class="stars" style="top:168px"><b>★★★</b>★★</div>
  </div>
  <div class="card" style="left:765px;top:703px;height:198px">
    <div class="pic" role="img" aria-label="Two lipsticks, red and black" style="left:60px;width:65px;background:linear-gradient(#e7322c 20%,#1d1d1d 21%)"></div>
    <div class="name">Kates rima kola pose</div><div class="price">$45.00</div>
    <div class="stars" style="top:168px"><b>★★★★</b>★</div>
  </div>
  <div class="card" style="left:970px;top:703px;height:198px">
    <div class="pic" role="img" aria-label="Pink perfume bottle with its box" style="background:linear-gradient(135deg,#f4b6d4,#ef8dbb)"></div>
    <div class="name">Yan mapon laten</div><div class="price">$67.00</div>
    <div class="stars" style="top:168px"><b>★★★</b>★★</div>
  </div>

  <div class="card" style="left:560px;top:925px;height:198px">
    <div class="pic" role="img" aria-label="Violet round perfume bottle" style="background:radial-gradient(circle at 50% 60%,#a9a1de,#5f57b0 70%,#fff)"></div>
    <div class="name">Vurem moren tikas</div><div class="price">$77.00</div>
    <div class="stars" style="top:168px"><b>★★</b>★★★</div>
  </div>
  <div class="card" style="left:765px;top:925px;height:198px">
    <div class="pic" role="img" aria-label="Gold-capped rosy perfume bottle" style="background:linear-gradient(#d9a93a 25%,#f7e6dc 26%,#efc7b4)"></div>
    <div class="name">Vopi jare mase lamas</div><div class="price">$99.00</div>
    <div class="stars" style="top:168px"><b>★★★★</b>★</div>
  </div>
  <div class="card" style="left:970px;top:925px;height:209px">
    <div class="pic" role="img" aria-label="Green perfume bottle with green box" style="background:linear-gradient(135deg,#1f8a3a,#46c35a)"></div>
    <div class="name">Futen moten katen rigas</div><div class="price">$56.00</div>
    <div class="stars" style="top:180px"><b>★★★★</b>★</div>
  </div>

  <div class="toolbar" style="top:1146px;border-bottom:2px solid var(--accent)">
    <div class="grid-ic"></div><div class="list-ic"></div>
    <span class="abs" style="left:58px;top:12px">Sort by</span>
    <div class="sel" style="left:89px;width:65px">Position ▾</div>
    <span class="abs" style="left:157px;top:8px;font-size:11px">↓</span>
    <span class="abs" style="left:396px;top:12px">Show</span>
    <div class="sel" style="left:425px;width:30px">12 ▾</div>
    <span class="abs" style="left:461px;top:12px">per page</span>
    <div class="pg on" style="left:503px">1</div><div class="pg" style="left:525px">2</div><div class="pg" style="left:546px">3</div><div class="pg" style="left:567px">›</div>
  </div>

  <!-- Footer -->
  <div class="footer"></div>
  <div class="news"></div>
  <div class="abs" style="left:559px;top:1215px;width:1px;height:257px;background:#e2e2e2"></div>
  <div class="abs fcol" style="left:349px;top:1235px"><h4>About the Shop</h4></div>
  <p class="abs ftext" style="left:348px;top:1268px;width:190px">Lorem ipsum dolor sit amet, consectetur adipisci elit. Pellentesque vulputate iaculis dolor. Nam con vallis porttitor sapien, ut tincidunt magna</p>
  <div class="abs ftext" style="left:348px;top:1315px;line-height:16px">
    <div><span style="color:var(--accent)">●</span>&nbsp; Add: 27 Harbor Lane, Fairview, Westbay</div>
    <div><span style="color:var(--accent)">●</span>&nbsp; Tel: +100 555 0142</div>
    <div><span style="color:var(--accent)">●</span>&nbsp; Email: hello@larkspur.example</div>
  </div>
  <div class="abs fcol" style="left:348px;top:1374px"><h4>Follow Us</h4></div>
  <p class="abs ftext" style="left:348px;top:1404px;width:180px">At vero eos et accusamus et iusto odio dignissimos ducimus qui blanditiis</p>
  <div class="soc" style="left:348px;background:#f5b324"></div>
  <div class="soc" style="left:372px;background:#7fd3e6"></div>
  <div class="soc" style="left:396px;background:#3aa1e2"></div>
  <div class="soc" style="left:420px;background:#3b5a9a"></div>
  <div class="soc" style="left:444px;background:#e2685a"></div>

  <div class="abs" style="left:576px;top:1243px;font-size:11px;font-weight:500">NEWSLETTER SIGN UP</div>
  <div class="abs" style="left:701px;top:1236px;width:373px;height:27px;background:#fff;border:1px solid var(--rule);font-size:8.5px;color:#999;padding:8px 7px">Enter your email...</div>
  <div class="abs" style="left:1073px;top:1236px;width:81px;height:27px;background:var(--accent);color:#fff;font-size:10px;text-align:center;line-height:27px">SUBSCRIBE</div>

  <div class="abs fcol" style="left:580px;top:1307px"><h4>Information</h4><ul><li>About Us</li><li>Contact Us</li><li>Terms &amp; Conditions</li><li>Privacy Policy</li><li>Orders and Returns</li><li>Site Map</li></ul></div>
  <div class="abs fcol" style="left:729px;top:1307px"><h4>Why Choose Us</h4><ul><li>Product Recall</li><li>Gift Vouchers</li><li>Returns and Exchanges</li><li>Shipping Options</li><li>Help &amp; FAQs</li><li>Hard to Find Parts</li></ul></div>
  <div class="abs fcol" style="left:877px;top:1307px"><h4>My Account</h4><ul><li>Sign In</li><li>View Cart</li><li>My Wishlist</li><li>Check out</li><li>Track My Order</li><li>Help</li></ul></div>
  <div class="abs fcol" style="left:1025px;top:1307px"><h4>Customer Services</h4><ul><li>Pricing Policy</li><li>Shipping Policy</li><li>Payment Methods</li><li>Site Information</li><li>Site Information</li><li>Payment Methods</li></ul></div>

  <div class="copy">© 2016 .All Rights Reserved.</div>
  <div class="pay" style="left:1003px"></div>
  <div class="pay" style="left:1034px"></div>
  <div class="pay" style="left:1066px"></div>
  <div class="pay" style="left:1097px"></div>
  <div class="pay" style="left:1129px"></div>
</div>
</body>
</html>
```